New letter head for Air Conditioning business

We need a new professional letter head design to suit our new re-branded air conditioning business. Our new logo is attached

```html
<!DOCTYPE html>
<html lang="en">
<head>
<meta charset="utf-8">
<title>Alderby Letterhead</title>
<link rel="stylesheet" href="https://fonts.googleapis.com/css2?family=Lato:wght@300;400;700&family=Pinyon+Script&display=swap">
<style>
  :root {
    --backdrop: #e4e4e4;
    --paper: #f1f1f1;
    --ink: #2f2f2f;
    --text: #4a4a4a;
    --body: #555555;
    --brand-green: #5bb47f;
    --brand-dark: #333333;
  }
  * { box-sizing: border-box; margin: 0; padding: 0; }
  html, body { width: 1200px; height: 1200px; overflow: hidden; }
  body {
    background: var(--backdrop);
    font-family: "Lato", Arial, sans-serif;
    position: relative;
  }
  .letterhead {
    position: absolute;
    left: 197px; top: 30px;
    width: 806px; height: 1140px;
    background: var(--paper);
    box-shadow: 0 4px 14px rgba(0,0,0,0.12);
  }
  .brand {
    position: absolute;
    left: 55px; top: 62px;
    display: flex; align-items: center; gap: 12px;
  }
  .brand-dot {
    width: 30px; height: 30px; border-radius: 50%;
    background: var(--brand-green);
  }
  .brand-name {
    font-weight: 700; font-size: 30px; letter-spacing: 3px;
    color: var(--brand-dark);
  }
  .contact {
    position: absolute;
    left: 555px; top: 42px;
    height: 100px;
    border-left: 2px solid var(--brand-green);
    padding-left: 22px;
    font-size: 13px; line-height: 16.5px;
    color: var(--text);
  }
  .contact address { font-style: normal; margin-bottom: 4px; }
  .contact-line { display: flex; align-items: center; gap: 6px; }
  .contact-line svg { width: 10px; height: 10px; fill: var(--brand-green); }
  .letter {
    position: absolute;
    left: 86px; top: 265px;
    width: 634px;
    font-size: 12.6px; font-weight: 300;
    color: var(--body);
  }
  .date { margin-bottom: 25px; }
  .recipient { line-height: 19px; margin-bottom: 38px; }
  .recipient strong { font-weight: 700; color: #111; }
  .salutation { margin-bottom: 19px; }
  .letter p.body-copy {
    text-align: justify; line-height: 19px; margin-bottom: 19px;
  }
  .closing { margin-top: 48px; }
  .signature {
    font-family: "Pinyon Script", cursive;
    font-size: 27px; color: #222; margin-top: 6px; padding-left: 6px;
  }
</style>
</head>
<body>
  <main class="letterhead">
    <header>
      <div class="brand">
        <span class="brand-dot"></span>
        <span class="brand-name">ALDERBY</span>
      </div>
      <div class="contact">
        <address>Unit 48, Level 2<br>Block D, Harrowfield Rd<br>NSW, Australia 2100</address>
        <div class="contact-line">
          <svg viewBox="0 0 10 10"><path d="M2 0.5 L3.6 2.6 L2.7 3.6 Q3.8 6 6.4 7.3 L7.4 6.4 L9.5 8 L8.3 9.6 Q3.5 9 0.4 1.7 Z"/></svg>
          <span>(+1) 555.010.2040</span>
        </div>
        <div class="contact-line">
          <svg viewBox="0 0 10 10"><path d="M0 2 H10 V8 H0 Z M0.6 2.5 L5 5.6 L9.4 2.5" stroke="#f1f1f1" stroke-width="0.8"/></svg>
          <span>info@alderbyair.com</span>
        </div>
        <div class="contact-line">
          <svg viewBox="0 0 10 10"><circle cx="5" cy="5" r="4.5" fill="none" stroke="#5bb47f" stroke-width="1"/><path d="M0.5 5 H9.5 M5 0.5 V9.5" stroke="#5bb47f" stroke-width="0.8"/></svg>
          <span>www.alderbyair.com</span>
        </div>
      </div>
    </header>

    <section class="letter">
      <p class="date">01 January 2050</p>
      <p class="recipient"><strong>Company (Pvt) Ltd.</strong><br>PO Box 3355 Mainville St<br>Sample City Country 3355</p>
      <p class="salutation">Dear Daniel Ashworth,</p>
      <p class="body-copy">Lorem ipsum dolor sit amet, consectetuer adipiscing elit, sed diam nonummy nibh euismod tincidunt ut laoreet dolore magna aliquam erat volutpat. Ut wisi enim ad minim veniam, quis nostrud exerci tation ullamcorper suscipit lobortis nisl ut aliquip ex ea commodo consequat. Duis dolore te feugait nulla facilisi. Nam liber tempor cum soluta nobis eleifend option congue nihil imperdiet doming id quod mazim placerat facer possim assum. Lorem ipsum dolor sit amet, consectetuer adipiscing elit, sed diam nonummy nibh euismod tincidunt ut laoreet dolore magna aliquam erat volutpat. Ut wisi enim ad minim veniam, quis nostrud exerci tation ullamcorper suscipit lobortis nisl ut aliquip ex ea commodo consequat.</p>
      <p class="body-copy">Consectetuer adipiscing elit, sed diam nonummy nibh euismod tincidunt ut laoreet dolore magna aliquam erat volutpat. Ut wisi enim ad minim veniam, quis nostrud exerci tation ullamcorper suscipit lobortis nisl ut aliquip ex ea commodo consequat. Consectetuer adipiscing elit, sed diam nonummy nibh euismod tincidunt ut laoreet dolore magna aliquam erat volutpat. Ut wisi enim ad minim veniam, quis nostrud exerci tation ullamcorper suscipit lobortis nisl ut aliquip ex ea commodo consequat.</p>
      <p class="body-copy">Consectetuer adipiscing elit, sed diam nonummy nibh euismod tincidunt ut laoreet dolore magna aliquam erat volutpat. Ut wisi enim ad minim veniam, quis nostrud exerci tation ullamcorper suscipit lobortis nisl ut aliquip ex ea commodo consequat. Consectetuer adipiscing elit, sed diam nonummy nibh euismod tincidunt ut laoreet dolore magna aliquam erat volutpat. Ut wisi enim ad minim veniam, quis nostrud exerci tation ullamcorper suscipit lobortis nisl ut aliquip ex ea commodo consequat.</p>
      <p class="closing">Sincerely Yours</p>
      <p class="signature">Thomas Edward Carlow</p>
    </section>
  </main>
</body>
</html>
```